Business Card for Professional Photographer

I'm looking for an eye catching modern clean design that compliments my logo/ website fonts & colours.
I specialise in architecture, corporate & commercial photography so I'm marketing to professional clients rather than portrait / wedding clients.

I would prefer to not have a solid black design.

My logo brand guide is as follows :

Main front font. : Reislust
Main font colour : #fff
Slogan front font : Ubuntu Bold
Monogram front font : Venti Medium
Container colour : #fff

I need print ready files in pdf .png & .eps formats.

Included in the files below are some screen grabs as reference to font & colours etc.

```html
<!DOCTYPE html>
<html lang="en">
<head>
<meta charset="utf-8">
<title>Quiet Angle – Business Card</title>
<link rel="stylesheet" href="https://fonts.googleapis.com/css2?family=Ubuntu:wght@400;500&family=Roboto:wght@400&family=Saira+Semi+Condensed:wght@600&display=swap">
<style>
  :root {
    --backdrop: #b5b5b5;
    --gold-deep: #b08c45;
    --gold-mid: #cdb168;
    --gold-light: #e8da96;
    --gold-text: #a9843a;
    --ink: #1a1a1a;
    --ink-soft: #333333;
    --card-white: #f6f6f6;
  }
  * { margin: 0; padding: 0; box-sizing: border-box; }
  html, body {
    width: 1200px; height: 576px; overflow: hidden;
    background: var(--backdrop);
  }
  .canvas { position: relative; width: 1200px; height: 576px; }

  .card { position: absolute; border-radius: 10px; overflow: hidden; }

  /* Front */
  .card--front {
    left: 80px; top: 138px; width: 486px; height: 294px;
    background: linear-gradient(200deg, var(--gold-light) 0%, var(--gold-mid) 45%, var(--gold-deep) 100%);
  }
  .front__lockup {
    position: absolute; left: 0; right: 0; top: 116px;
    display: flex; flex-direction: column; align-items: center;
  }
  .front__brand {
    display: flex; align-items: center; gap: 12px;
    font-family: "Ubuntu", sans-serif; font-weight: 500;
    font-size: 26px; letter-spacing: 0.5px; color: var(--ink);
    line-height: 1;
  }
  .front__brand-square { width: 14px; height: 14px; background: var(--ink); }
  .front__tagline {
    margin-top: 12px;
    font-family: "Ubuntu", sans-serif; font-weight: 400;
    font-size: 11px; letter-spacing: 0.4px; color: var(--ink-soft);
    line-height: 1;
  }
  .front__web {
    position: absolute; left: 0; right: 0; top: 259px;
    text-align: center;
    font-family: "Ubuntu", sans-serif; font-weight: 400;
    font-size: 13px; letter-spacing: 2px; color: var(--ink-soft);
  }

  /* Back */
  .card--back {
    left: 602px; top: 138px; width: 481px; height: 292px;
    background: var(--card-white);
  }
  .back__name {
    position: absolute; left: 27px; top: 55px;
    font-family: "Saira Semi Condensed", sans-serif; font-weight: 600;
    font-size: 19px; color: var(--gold-text); line-height: 1;
  }
  .back__role {
    position: absolute; left: 27px; top: 80px;
    font-family: "Roboto", sans-serif; font-size: 12.5px; color: var(--ink-soft);
  }
  .back__lockup {
    position: absolute; left: 255px; width: 210px; top: 112px;
    display: flex; flex-direction: column; align-items: center;
  }
  .back__brand {
    display: flex; align-items: center; gap: 10px;
    font-family: "Ubuntu", sans-serif; font-weight: 500;
    font-size: 22px; letter-spacing: 0.5px; color: var(--gold-text);
    line-height: 1;
  }
  .back__brand-square { width: 12px; height: 12px; background: var(--gold-text); }
  .back__tagline {
    margin-top: 10px;
    font-family: "Ubuntu", sans-serif; font-weight: 400;
    font-size: 9.5px; letter-spacing: 0.3px; color: var(--ink-soft);
    line-height: 1;
  }
  .contact-list {
    position: absolute; left: 29px; top: 198px;
    list-style: none;
    font-family: "Roboto", sans-serif; font-size: 12.5px; color: var(--ink);
  }
  .contact-list li { display: flex; align-items: center; height: 18.5px; }
  .contact-list svg { width: 11px; height: 11px; margin-right: 12px; }
  .back__band { position: absolute; left: 0; bottom: 0; width: 481px; height: 40px; }
  .back__address {
    position: absolute; left: 262px; top: 266px;
    font-family: "Roboto", sans-serif; font-size: 12.5px; color: var(--ink);
  }
</style>
</head>
<body>
<main class="canvas">

  <section class="card card--front" aria-label="Card front">
    <div class="front__lockup">
      <div class="front__brand"><span class="front__brand-square"></span>Quiet Angle</div>
      <div class="front__tagline">Built Spaces &amp; Business Imagery</div>
    </div>
    <div class="front__web">www.quietangle.com.au</div>
  </section>

  <section class="card card--back" aria-label="Card back">
    <div class="back__name">Marcus Hale</div>
    <div class="back__role">Photographer</div>

    <div class="back__lockup">
      <div class="back__brand"><span class="back__brand-square"></span>Quiet Angle</div>
      <div class="back__tagline">Built Spaces &amp; Business Imagery</div>
    </div>

    <ul class="contact-list">
      <li>
        <svg viewBox="0 0 12 12" aria-hidden="true"><path d="M1 3c0-1 1-2 2-2h6c1 0 2 1 2 2v1H8V3H4v1H1z M2 5h8l1 6H1z" fill="var(--gold-mid)"/></svg>
        0400123456
      </li>
      <li>
        <svg viewBox="0 0 12 12" aria-hidden="true"><rect x="0.5" y="2" width="11" height="8" fill="var(--gold-mid)"/><path d="M0.5 2L6 6.5 11.5 2" stroke="#fff" stroke-width="1" fill="none"/></svg>
        hello@quietangle.com.au
      </li>
      <li>
        <svg viewBox="0 0 12 12" aria-hidden="true"><circle cx="6" cy="6" r="5.2" fill="var(--gold-mid)"/><path d="M1 6h10M6 1v10M3 3.2h6M3 8.8h6" stroke="#fff" stroke-width="0.7"/><ellipse cx="6" cy="6" rx="2.3" ry="5.2" stroke="#fff" stroke-width="0.7" fill="none"/></svg>
        www.quietangle.com.au
      </li>
    </ul>

    <svg class="back__band" viewBox="0 0 481 40" aria-hidden="true">
      <defs>
        <linearGradient id="bandGold" x1="0" x2="1" y1="0" y2="0">
          <stop offset="0" stop-color="var(--gold-deep)"/>
          <stop offset="0.6" stop-color="var(--gold-light)"/>
          <stop offset="1" stop-color="var(--gold-mid)"/>
        </linearGradient>
      </defs>
      <rect x="0" y="26" width="481" height="14" fill="url(#bandGold)"/>
      <polygon points="218,40 238,5 481,5 481,40" fill="url(#bandGold)"/>
    </svg>
    <div class="back__address">48 Harbour Rd Lakeside Vic 3999</div>
  </section>

</main>
</body>
</html>
```